Silvermoor Property Development Co.

We need a logo and business card design for a Hong Kong based real estate company, PLX Land. We are want the brand to reflect the owners forward thinking, creative, and trend setting projects, while also reflecting a sense of security and strength. We invest in industrial properties which we convert to co-living or co-working spaces. PLX stands for Greater Bay Area which is the region around southern China including HK, Macau, and 9 other Chinese cities...made up of approx. 68 million people. There are massive infrastructure projects including the bridge to Macau and high-speed rail to SZ and the bridge connecting SZ and Zhongshan.

Target Market(s)

Chinese and western retail investors, as well as institutional investors

Industry/Entity Type

Real Estate Development

Contact Information for Business Card

Dale Whitford
CEO
dale@plxland-example.com
M + 852 9581 4062
F + 852 3864 2217
Suite 2207, The Halvern, 41 Tremont Rd., Central, Hong Kong

Logo Text

plx land (company name) lifestyle property development (underneath)

Colors

Designer to choose colors to be used in the design.

Requirements
Must have
• Details listed above. One side should include the logo and company name...plx land in modern, hip styling with "lifestyle property development"
Nice to have
• Could be a Black card, with metallic purple "plx" and white "land"...but open great design ideas
Should not have
• boring and traditional layout

```html
<!DOCTYPE html>
<html lang="en">
<head>
<meta charset="utf-8">
<title>PLX Land – Business Card</title>
<link rel="stylesheet" href="https://fonts.googleapis.com/css2?family=Oswald:wght@500&family=Work+Sans:wght@400&display=swap">
<style>
  :root {
    --backdrop: #1d1d1e;
    --card: #121213;
    --card-edge: #1a1a1b;
    --ink: #ffffff;
    --ink-soft: #d9d9d9;
  }
  html, body {
    margin: 0;
    width: 1200px;
    height: 900px;
    overflow: hidden;
    background: var(--backdrop);
  }
  .canvas {
    position: relative;
    width: 1200px;
    height: 900px;
  }
  .card {
    position: absolute;
    left: 260px;
    width: 680px;
    height: 388px;
    background: linear-gradient(135deg, var(--card) 0%, var(--card-edge) 60%, var(--card) 100%);
    box-shadow: 0 10px 30px rgba(0,0,0,0.45);
    color: var(--ink);
  }
  .card--front { top: 50px; }
  .card--back { top: 462px; }

  .brand {
    position: absolute;
    left: 70px;
    top: 132px;
  }
  .brand__row {
    display: flex;
    align-items: center;
    gap: 18px;
  }
  .brand__square {
    width: 22px;
    height: 22px;
    background: var(--ink);
  }
  .brand__name {
    font-family: "Work Sans", sans-serif;
    font-weight: 400;
    font-size: 58px;
    line-height: 1;
    letter-spacing: 0;
    margin: 0;
  }
  .brand__tagline {
    font-family: "Work Sans", sans-serif;
    font-weight: 400;
    font-size: 18px;
    letter-spacing: 0.5px;
    color: var(--ink-soft);
    margin: 18px 0 0 40px;
  }

  .person {
    position: absolute;
    right: 418px;
    top: 128px;
    text-align: right;
  }
  .person__name {
    font-family: "Oswald", sans-serif;
    font-weight: 500;
    font-size: 36px;
    line-height: 1;
    letter-spacing: 1px;
    margin: 0;
    white-space: nowrap;
  }
  .person__title {
    font-family: "Work Sans", sans-serif;
    font-size: 15px;
    color: var(--ink-soft);
    letter-spacing: 1px;
    margin: 6px 2px 0 0;
  }
  .divider {
    position: absolute;
    left: 300px;
    top: 126px;
    width: 2px;
    height: 64px;
    background: var(--ink);
  }
  .contacts {
    position: absolute;
    left: 340px;
    top: 128px;
    margin: 0;
    padding: 0;
    list-style: none;
    font-family: "Work Sans", sans-serif;
    font-size: 18px;
    line-height: 24px;
    letter-spacing: 0.5px;
    white-space: nowrap;
  }
  .contacts li {
    display: flex;
    align-items: center;
    gap: 12px;
  }
  .contacts svg {
    width: 12px;
    height: 12px;
    fill: none;
    stroke: var(--ink);
    stroke-width: 1.4;
  }
  .address {
    position: absolute;
    left: 46px;
    bottom: 48px;
    margin: 0;
    font-family: "Work Sans", sans-serif;
    font-size: 18px;
    letter-spacing: 0.5px;
    white-space: nowrap;
  }
</style>
</head>
<body>
<main class="canvas">
  <section class="card card--front" aria-label="Card front">
    <div class="brand">
      <div class="brand__row">
        <span class="brand__square"></span>
        <h1 class="brand__name">PLX Land</h1>
      </div>
      <p class="brand__tagline">Lifestyle property development</p>
    </div>
  </section>

  <section class="card card--back" aria-label="Card back">
    <div class="person">
      <h2 class="person__name">DALE WHITFORD</h2>
      <p class="person__title">CEO</p>
    </div>
    <div class="divider"></div>
    <ul class="contacts">
      <li>
        <svg viewBox="0 0 12 12" aria-label="Mobile"><path d="M2.5 1.5 L4.5 1.5 L5.2 3.8 L4 4.8 Q5 7 7.2 8 L8.2 6.8 L10.5 7.5 L10.5 9.5 Q10.5 10.5 9.5 10.5 Q2 10 1.5 2.5 Q1.5 1.5 2.5 1.5 Z"/></svg>
        <span>+ 852 9581 4062</span>
      </li>
      <li>
        <svg viewBox="0 0 12 12" aria-label="Fax"><rect x="3" y="1.5" width="6" height="3.5"/><rect x="1.5" y="5" width="9" height="4"/><rect x="3" y="8" width="6" height="2.5"/></svg>
        <span>+ 852 3864 2217</span>
      </li>
      <li>
        <svg viewBox="0 0 12 12" aria-label="Email"><rect x="1.5" y="2.5" width="9" height="7"/><path d="M1.5 2.5 L6 6.5 L10.5 2.5"/></svg>
        <span>dale@plxland-example.com</span>
      </li>
    </ul>
    <p class="address">Suite 2207, The Halvern, 41 Tremont Rd., Central, Hong Kong</p>
  </section>
</main>
</body>
</html>
```